Calvanto Group Real Estate Company business cards

New business card design, we are generally happy with the basic layout of the existing front of business card, (feel free to change) but require a head shot photo on the back side.

http://www.calvanto.com.au/

Attached logos, and existing business card

------------------------------

Target Market(s)

Real estate

Industry/Entity Type

Real Estate

Contact Information for Business Card

Standard size double sided

Font styles to use
Other font styles liked:
• Futura

Requirements
Must have
• Photo head shot on the back side
Nice to have
• yes
Should not have
• No

```html
<!DOCTYPE html>
<html lang="en">
<head>
<meta charset="utf-8">
<title>Calvanto Group – Business Cards</title>
<link href="https://fonts.googleapis.com/css2?family=Jost:wght@400;500;700&display=swap" rel="stylesheet">
<style>
  :root {
    --bg: #1c1c1c;
    --card: #ffffff;
    --purple: #3a2a6e;
    --orange: #f39021;
    --orange-light: #f7b060;
    --grey: #8a8a8a;
    --ink: #222222;
    --suit: #2f3a55;
    --skin: #d9b59a;
  }
  html, body {
    margin: 0;
    width: 1200px;
    height: 910px;
    overflow: hidden;
    background: var(--bg);
    font-family: "Jost", "Futura", sans-serif;
  }
  .sheet {
    position: relative;
    width: 1200px;
    height: 910px;
  }
  .card {
    position: absolute;
    left: 250px;
    width: 700px;
    height: 400px;
    background: var(--card);
    border-radius: 22px;
    overflow: hidden;
  }
  .card--photo { top: 37px; }
  .card--contact { top: 473px; }

  .wordmark {
    position: absolute;
    color: var(--purple);
    font-weight: 500;
    font-size: 78px;
    line-height: 1;
    letter-spacing: 1px;
  }
  .wordmark__sub {
    position: absolute;
    color: var(--grey);
    font-size: 13px;
    letter-spacing: 9px;
  }
  .card--photo .wordmark { left: 60px; top: 92px; }
  .card--photo .wordmark__sub { left: 252px; top: 180px; }
  .services {
    position: absolute;
    left: 62px;
    top: 228px;
    font-size: 17px;
    font-weight: 500;
    color: var(--ink);
    letter-spacing: 0.5px;
  }
  .headshot {
    position: absolute;
    right: 0;
    bottom: 0;
    width: 290px;
    height: 330px;
    background:
      radial-gradient(ellipse 70px 85px at 58% 32%, var(--skin) 0%, var(--skin) 85%, transparent 100%),
      linear-gradient(180deg, #ffffff 0%, #ffffff 45%, var(--suit) 62%, #243048 100%);
  }

  .person {
    position: absolute;
    left: 44px;
    top: 44px;
    z-index: 1;
  }
  .person__name {
    margin: 0;
    font-size: 22px;
    font-weight: 700;
    color: var(--purple);
  }
  .person__role {
    margin: 0;
    font-size: 16px;
    color: var(--ink);
  }
  .contact-list {
    list-style: none;
    margin: 18px 0 0;
    padding: 0;
    font-size: 18px;
    color: var(--ink);
  }
  .contact-list li {
    display: flex;
    align-items: center;
    gap: 10px;
    margin-bottom: 4px;
  }
  .contact-list svg { width: 16px; height: 16px; flex: none; }

  .card--contact .wordmark { right: 50px; top: 110px; }
  .card--contact .wordmark__sub { right: 42px; top: 198px; }

  .wave { position: absolute; left: 0; top: 0; }
  .company {
    position: absolute;
    right: 46px;
    bottom: 24px;
    text-align: right;
    color: var(--purple);
    font-size: 21px;
    line-height: 1.25;
    z-index: 1;
  }
  .company p { margin: 0; }
</style>
</head>
<body>
<main class="sheet">

  <section class="card card--photo" aria-label="Card side with headshot">
    <div class="wordmark">calvanto</div>
    <div class="wordmark__sub">GROUP</div>
    <div class="services">BUY | SELL | RENT</div>
    <div class="headshot" role="img" aria-label="Headshot photo of the director in a navy suit and blue tie"></div>
  </section>

  <section class="card card--contact" aria-label="Card side with contact details">
    <svg class="wave" width="700" height="400" viewBox="0 0 700 400" aria-hidden="true">
      <defs>
        <linearGradient id="orangeBand" x1="0" y1="0" x2="1" y2="0">
          <stop offset="0" stop-color="var(--orange)"/>
          <stop offset="0.55" stop-color="var(--orange-light)"/>
          <stop offset="1" stop-color="var(--orange)"/>
        </linearGradient>
      </defs>
      <path d="M0 255 C 120 290, 260 338, 420 328 C 550 318, 640 296, 700 280 L700 400 L0 400 Z" fill="url(#orangeBand)"/>
      <path d="M0 235 C 120 275, 260 325, 420 315 C 550 305, 640 285, 700 268" fill="none" stroke="var(--purple)" stroke-width="6"/>
    </svg>

    <div class="person">
      <p class="person__name">Daniel Tran</p>
      <p class="person__role">Director</p>
      <ul class="contact-list">
        <li>
          <svg viewBox="0 0 16 16" aria-hidden="true"><rect x="4" y="1" width="8" height="14" rx="1.5" fill="none" stroke="var(--purple)" stroke-width="1.6"/><circle cx="8" cy="12.5" r="0.9" fill="var(--purple)"/></svg>
          <span>0400 555 218</span>
        </li>
        <li>
          <svg viewBox="0 0 16 16" aria-hidden="true"><rect x="1" y="3" width="14" height="10" fill="var(--purple)"/><path d="M1 3 L8 9 L15 3" fill="none" stroke="#fff" stroke-width="1.2"/></svg>
          <span>daniel.tran@calvanto.com.au</span>
        </li>
        <li>
          <svg viewBox="0 0 16 16" aria-hidden="true"><circle cx="8" cy="8" r="6.5" fill="none" stroke="var(--purple)" stroke-width="1.4"/><ellipse cx="8" cy="8" rx="3" ry="6.5" fill="none" stroke="var(--purple)" stroke-width="1.1"/><path d="M1.5 8 H14.5" stroke="var(--purple)" stroke-width="1.1"/></svg>
          <span>www.calvanto.com.au</span>
        </li>
      </ul>
    </div>

    <div class="wordmark">calvanto</div>
    <div class="wordmark__sub">GROUP</div>

    <div class="company">
      <p>Calvanto Group</p>
      <p>ABN: 12 345 678 901</p>
    </div>
  </section>

</main>
</body>
</html>
```